New Fun, Positive, energised looking Business Card Needed for High Achiever Coach

I am looking for a two sided full colour business card. I am self employed and have recently re branded my 1-2-1 work re-vitalising high achievers. My target client base for these cards is therefore high achievers - usually aged 40 -55, they are often entrepreneurs, CEO or work in banking and finance and 2/3 are male. I work with them on 90 day or 6 month coaching programs to help them live their success in a healthier, more sustainable and fulfiiled way. They pay for this privately so though they are corporate types the cards need not look 'corporate'. I want to portray the idea of transformation, vitality and re-connecting.
You can get a feel for the look I like on my new website: morvenlisk.co.uk
I want to use this logo with strapline (Re-Vitalising High Achievers) (I purchased off Logoharbor) and font/ colours (the turquoise and green).
Details to include on the card:
www.morvenlisk.co.uk
+44 7915 302618
morven@morvenlisk.co.uk
skype: morvenlisk
I'd also like to include:
Do you struggle to switch off? Want to be healthier and feel fitter? Want closer relationships? More clarity over the direction you are headed? I can help you do these things using integrated mind-body techniques. Visit morvenlisk.co.uk TODAY to apply for a FREE Breakthrough session.
BUT if that is too much text for a card I am open to advice/ammendments.
Updates
Thanks for your design - I am considering them. PLease change the wording to :

```html
<!DOCTYPE html>
<html lang="en">
<head>
<meta charset="utf-8">
<title>Morven Lisk – Business Card</title>
<link rel="stylesheet" href="https://fonts.googleapis.com/css2?family=Open+Sans:wght@400;600;700&display=swap">
<style>
  :root {
    --turquoise: #18a4cf;
    --green: #62b96c;
    --white: #ffffff;
    --stage: #eeece8;
    --name-blue: #1b9fc6;
    --shadow: rgba(0, 0, 0, 0.18);
  }
  * { box-sizing: border-box; margin: 0; padding: 0; }
  html, body { width: 1200px; height: 720px; overflow: hidden; }
  body {
    background: var(--stage);
    font-family: "Open Sans", Arial, sans-serif;
    display: flex;
    align-items: center;
    justify-content: center;
    gap: 40px;
  }
  .card {
    width: 540px;
    height: 327px;
    position: relative;
    overflow: hidden;
    box-shadow: 0 6px 18px var(--shadow);
  }

  /* Front side */
  .card-front { display: flex; background: var(--turquoise); }
  .brand-panel {
    width: 258px;
    background: var(--white);
    border-right: 4px solid var(--green);
    display: flex;
    flex-direction: column;
    align-items: center;
    justify-content: center;
    gap: 6px;
  }
  .brand-name {
    display: flex;
    align-items: center;
    gap: 10px;
    font-weight: 700;
    font-size: 30px;
    color: var(--name-blue);
    letter-spacing: 0.5px;
  }
  .brand-dot {
    width: 22px; height: 22px;
    border-radius: 50%;
    background: var(--green);
  }
  .strapline {
    font-size: 13px;
    font-weight: 400;
    color: var(--name-blue);
  }
  .contact-panel { flex: 1; padding: 30px 0 0 26px; }
  .contact-list { list-style: none; color: var(--white); font-size: 14px; }
  .contact-list li {
    display: flex;
    align-items: center;
    gap: 9px;
    line-height: 1.65;
  }
  .contact-icon { width: 14px; height: 14px; flex: none; }

  /* Back side */
  .card-back { background: var(--turquoise); color: var(--white); text-align: center; }
  .question-band {
    height: 154px;
    background: var(--green);
    display: flex;
    align-items: flex-end;
    justify-content: center;
    padding-bottom: 10px;
  }
  .questions { font-size: 15.5px; line-height: 1.42; }
  .offer { padding-top: 20px; font-size: 15.5px; line-height: 1.42; }
  .offer p + p { margin-top: 6px; }
  .offer strong { font-weight: 700; }
</style>
</head>
<body>

  <section class="card card-front" aria-label="Business card front">
    <div class="brand-panel">
      <div class="brand-name"><span class="brand-dot"></span>Morven Lisk</div>
      <div class="strapline">Re-Vitalising High Achievers</div>
    </div>
    <div class="contact-panel">
      <ul class="contact-list">
        <li>
          <svg class="contact-icon" viewBox="0 0 16 16" aria-hidden="true"><circle cx="8" cy="8" r="7" fill="none" stroke="#fff" stroke-width="1.4"/><path d="M5.5 4.5l1.3 1.6-.8 1c.5 1 1.2 1.7 2.2 2.2l1-.8 1.6 1.3-.8 1.3C7.5 11 5 8.5 4.3 5.4z" fill="#fff"/></svg>
          +44 7915 302618
        </li>
        <li>
          <svg class="contact-icon" viewBox="0 0 16 16" aria-hidden="true"><circle cx="8" cy="8" r="8" fill="#fff"/><rect x="4" y="5.2" width="8" height="5.6" fill="none" stroke="#18a4cf" stroke-width="1.1"/><path d="M4 5.4l4 3 4-3" fill="none" stroke="#18a4cf" stroke-width="1.1"/></svg>
          morven@morvenlisk.co.uk
        </li>
        <li>
          <svg class="contact-icon" viewBox="0 0 16 16" aria-hidden="true"><circle cx="8" cy="8" r="8" fill="#fff"/><circle cx="8" cy="8" r="4.6" fill="none" stroke="#18a4cf" stroke-width="1"/><ellipse cx="8" cy="8" rx="2" ry="4.6" fill="none" stroke="#18a4cf" stroke-width="1"/><path d="M3.4 8h9.2" stroke="#18a4cf" stroke-width="1"/></svg>
          www.morvenlisk.co.uk
        </li>
        <li>
          <svg class="contact-icon" viewBox="0 0 16 16" aria-hidden="true"><circle cx="8" cy="8" r="8" fill="#fff"/></svg>
          morvenlisk
        </li>
      </ul>
    </div>
  </section>

  <section class="card card-back" aria-label="Business card back">
    <div class="question-band">
      <p class="questions">
        Do you struggle to switch off?<br>
        Want to be healthier and feel fitter?<br>
        Want closer relationships?<br>
        More clarity over the direction you are headed?
      </p>
    </div>
    <div class="offer">
      <p>I can help you do these things using integrated<br>mind-body techniques.</p>
      <p>Visit <strong>morvenlisk.co.uk</strong> TODAY to apply for a<br>FREE Breakthrough session.</p>
    </div>
  </section>

</body>
</html>
```